Marwick Law Letterhead

We need a new letterhead design for a Law Firm. The address for the law firm is 1475 Calloway Street, Suite 210, Houston, Texas 77041. Phone Number: 832-361-9027; Fax Number: 832-614-7359. The logo is uploaded to the project.

```html
<!DOCTYPE html>
<html lang="en">
<head>
<meta charset="utf-8">
<title>Marwick Law Letterhead</title>
<link href="https://fonts.googleapis.com/css2?family=Montserrat:wght@400;500;600&display=swap" rel="stylesheet">
<style>
  :root {
    --navy: #1f3a6e;
    --red: #c8151f;
    --ink: #1b1b1b;
    --paper: #ffffff;
    --backdrop: #e9e9eb;
  }
  * { box-sizing: border-box; margin: 0; padding: 0; }
  html, body { width: 1200px; height: 960px; overflow: hidden; }
  body {
    background: var(--backdrop);
    font-family: "Montserrat", Arial, sans-serif;
    color: var(--ink);
  }
  .letterhead {
    position: absolute;
    left: 290px; top: 41px;
    width: 620px; height: 877px;
    background: var(--paper);
    box-shadow: 0 4px 18px rgba(0,0,0,0.12);
    overflow: hidden;
  }
  .band { position: absolute; left: 0; width: 620px; height: 60px; }
  .band--top { top: 0; }
  .band--bottom { bottom: 0; }
  .brand {
    position: absolute; left: 40px; top: 66px;
    display: flex; align-items: center; gap: 10px;
  }
  .brand__mark { width: 22px; height: 22px; background: var(--navy); }
  .brand__name {
    font-weight: 600; font-size: 24px; color: var(--navy); letter-spacing: 0.5px;
  }
  .contact {
    position: absolute; right: 52px; top: 66px;
    border-left: 1px solid var(--red);
    padding-left: 12px;
    font-size: 10.5px; line-height: 1.45;
  }
  .contact__line { display: flex; align-items: center; gap: 6px; }
  .contact__line svg { width: 9px; height: 9px; flex: none; }
  .contact__address { margin-bottom: 3px; }
  .letter {
    position: absolute; left: 60px; top: 170px; width: 500px;
    font-size: 11px; line-height: 1.5;
  }
  .recipient { margin-bottom: 8px; }
  .letter p { margin-bottom: 16px; }
  .signoff { margin-top: 4px; font-size: 12px; }
  .signature {
    width: 110px; height: 34px; margin-top: 6px;
    background: linear-gradient(90deg, #f1f1f1, #e4e4e4);
    border-radius: 3px;
  }
</style>
</head>
<body>
  <main class="letterhead">
    <svg class="band band--top" viewBox="0 0 620 60" aria-hidden="true">
      <polygon points="0,0 620,0 620,14 240,14 220,46 0,46" fill="var(--navy)"/>
      <polygon points="246,20 620,20 620,26 242,26" fill="var(--red)"/>
    </svg>

    <div class="brand">
      <span class="brand__mark"></span>
      <span class="brand__name">Marwick Law</span>
    </div>

    <address class="contact">
      <div class="contact__address">1475 Calloway Street,<br>Suite 210, Houston,<br>Texas 77041</div>
      <div class="contact__line">
        <svg viewBox="0 0 10 10"><path d="M2 1 L4 1 L4.6 3 L3.4 3.8 Q4.6 5.8 6.2 6.6 L7 5.4 L9 6 L9 8 Q5 9 1.5 4.5 Q1 2.5 2 1Z" fill="var(--red)"/></svg>
        832-361-9027
      </div>
      <div class="contact__line">
        <svg viewBox="0 0 10 10"><rect x="3" y="1" width="4" height="3" fill="var(--red)"/><rect x="1" y="4" width="8" height="4" rx="1" fill="var(--red)"/><rect x="3" y="7" width="4" height="2" fill="var(--red)"/></svg>
        832-614-7359
      </div>
    </address>

    <section class="letter">
      <div class="recipient">Mr/s<br>First Name and Last Name<br>Company Name<br>Address</div>
      <p>Lorem ipsum dolor sit amet,consectetur adipiscing sed do eiusmod tempor incididunt laboreet dolore magna aliqua.Ut enim ad minim.veniam, quis nostrud exercitation ullamco laboris nisi ut aliquip exea commodo consequat.Lorem ipsum dolor sit amet,consectetur adipiscing sed do eiusmod tempor incididunt.labore et dolore magna aliqua. Ut enim</p>
      <p>Lorem ipsum dolor sit amet, consectetur adipiscing sed do eiusmod tempor incididunt labore et dolore magna aliqua. Ut enim ad minim veniam, quis nostrud exercitation ullamco laboris nisi ut aliquip exea commodo consequat.Duis aute irure dolor in reprehenderit in voluptate velit esse cillum irure dolor in reprehenderit in voluptate velit esse irure</p>
      <p>Lorem ipsum dolor sit amet, consectetur adipiscing sed do eiusmod tempor incididunt labore et dolore magna aliqua. consequat. Duis aute irure dolor in.reprehenderit in voluptate velit esse cillum dolore eu fugiat nulla pariatur. Excepteur sint occaecat cupidatat non proident, sunt in culpa qui officia deserunt mollit,</p>
      <p>Lorem ipsum dolor sit amet, consectetur adipiscing sed do eiusmod tempor incididunt labore et dolore magna aliqua. Ut enim Lorem ipsum dolor sit amet, consectetur adipiscing sed do eiusmod tempor incididunt labore et dolore magna aliqua. Ut enim Lorem ipsum aliqua.ipsum</p>
      <p>Lorem ipsum dolor sit amet, consectetur adipiscing sed do eiusmod tempor incididunt labore et dolore magna aliqua. Ut enim ad minim veniam, quis nostrud exercitation ullamco laboris nisi ut aliquip exea commodo consequat.Duis aute irure dolor in reprehenderit in voluptate velit esse cillum irure dolor in reprehenderit in voluptate velit esse irure</p>
      <p>Lorem ipsum dolor sit amet, consectetur adipiscing sed do eiusmod tempor incididunt labore et dolore magna aliqua. Ut enim ad minim veniam, quis nostrud exercitation ullamco laboris nisi ut aliquip exea commodo consequat.Duis aute irure dolor in reprehenderit in voluptate velit esse cillum irure dolor in reprehenderit in voluptate velit esse irure</p>
      <div class="signoff">Regards</div>
      <div class="signature" role="img" aria-label="Handwritten signature of the sender"></div>
    </section>

    <svg class="band band--bottom" viewBox="0 0 620 60" aria-hidden="true">
      <polygon points="620,60 0,60 0,46 380,46 400,14 620,14" fill="var(--navy)"/>
      <polygon points="374,40 0,40 0,34 378,34" fill="var(--red)"/>
    </svg>
  </main>
</body>
</html>
```